Maple Grove Schools | brand new stationery!

We need stationery design with our new logo! Our company updated it's name and image and we like to incorporate the new one on our stationery, business cards and email signature. We are looking for fresh, new ideas!
Industry: Childcare, Elementary and Middle School
Company Name: Maple Grove Schools
Tagline: Bright Futures Start Here
Main colors: Blue, white and a little yellow
Star shape is something new for us! Do you see a way to incorporate it as a design element?

```html
<!DOCTYPE html>
<html lang="en">
<head>
<meta charset="utf-8">
<title>Maple Grove Schools – Email Signature</title>
<link rel="stylesheet" href="https://fonts.googleapis.com/css2?family=Raleway:wght@500;600;700&family=Roboto:wght@400&display=swap">
<style>
  :root {
    --navy: #262b6b;
    --yellow: #f7b918;
    --text-grey: #5a5a5f;
    --logo-ink: #231f20;
    --paper: #ffffff;
    --backdrop: #d3d4d6;
  }
  * { box-sizing: border-box; margin: 0; padding: 0; }
  html, body {
    width: 1200px;
    height: 1200px;
    overflow: hidden;
    background: var(--backdrop);
  }
  .signature {
    position: absolute;
    left: 151px;
    top: 468px;
    width: 898px;
    height: 264px;
    background: var(--paper);
    overflow: hidden;
  }
  .signature__waves {
    position: absolute;
    inset: 0;
  }
  .brand {
    position: absolute;
    left: 118px;
    top: 42px;
    width: 240px;
    text-align: center;
    font-family: "Raleway", sans-serif;
    font-weight: 700;
    color: var(--logo-ink);
  }
  .brand__dot {
    display: block;
    width: 64px;
    height: 64px;
    margin: 0 auto 10px;
    border-radius: 50%;
    background: var(--navy);
  }
  .brand__name {
    font-size: 34px;
    line-height: 36px;
    letter-spacing: -0.3px;
  }
  .tagline {
    position: absolute;
    left: 40px;
    top: 226px;
    font-family: "Raleway", sans-serif;
    font-weight: 500;
    font-size: 13px;
    color: var(--paper);
  }
  .person {
    position: absolute;
    left: 389px;
    top: 38px;
    font-family: "Raleway", sans-serif;
  }
  .person__name {
    font-weight: 700;
    font-size: 20px;
    line-height: 24px;
    letter-spacing: 0.4px;
    color: var(--navy);
    text-transform: uppercase;
  }
  .person__role {
    font-weight: 500;
    font-size: 17px;
    line-height: 22px;
    color: var(--yellow);
  }
  .contacts {
    list-style: none;
    margin-top: 12px;
    font-family: "Roboto", sans-serif;
    font-size: 17px;
    color: var(--text-grey);
  }
  .contacts__item {
    display: flex;
    align-items: center;
    height: 25px;
  }
  .contacts__icon {
    width: 17px;
    height: 17px;
    margin-right: 6px;
    fill: var(--navy);
    flex: none;
  }
</style>
</head>
<body>
  <section class="signature">
    <svg class="signature__waves" viewBox="0 0 898 264" width="898" height="264" aria-hidden="true">
      <path d="M380 211 C 560 229 760 229 898 214 L898 222 C 760 235 560 234 380 212 Z" fill="var(--yellow)"/>
      <path d="M0 181 C 300 230 600 240 898 227 L898 264 L0 264 Z" fill="var(--navy)"/>
    </svg>

    <div class="brand">
      <span class="brand__dot"></span>
      <p class="brand__name">Maple Grove<br>Schools</p>
    </div>

    <p class="tagline">Bright Futures Start Here</p>

    <div class="person">
      <h1 class="person__name">Daniel R. Whitford</h1>
      <p class="person__role">Founder &amp; CEO</p>
      <ul class="contacts">
        <li class="contacts__item">
          <svg class="contacts__icon" viewBox="0 0 24 24" aria-hidden="true"><path d="M6.6 10.8a15.1 15.1 0 0 0 6.6 6.6l2.2-2.2a1 1 0 0 1 1-.25 11.4 11.4 0 0 0 3.6.57 1 1 0 0 1 1 1V20a1 1 0 0 1-1 1A17 17 0 0 1 3 4a1 1 0 0 1 1-1h3.5a1 1 0 0 1 1 1c0 1.25.2 2.45.57 3.57a1 1 0 0 1-.25 1z"/></svg>
          (555) 318-4720
        </li>
        <li class="contacts__item">
          <svg class="contacts__icon" viewBox="0 0 24 24" aria-hidden="true"><path d="M2 5h20v14H2z M4 7v.4l8 5.3 8-5.3V7z M4 9.8V17h16V9.8l-8 5.3z" fill-rule="evenodd"/></svg>
          hello@maplegroveschools.com
        </li>
        <li class="contacts__item">
          <svg class="contacts__icon" viewBox="0 0 24 24" aria-hidden="true"><path d="M12 2a10 10 0 1 0 0 20 10 10 0 0 0 0-20zm6.9 9h-3a15 15 0 0 0-1.4-6.3A8 8 0 0 1 18.9 11zM12 4.1c.9 1.2 1.8 3.6 1.9 6.9h-3.8c.1-3.3 1-5.7 1.9-6.9zM9.5 4.7A15 15 0 0 0 8.1 11h-3a8 8 0 0 1 4.4-6.3zM5.1 13h3a15 15 0 0 0 1.4 6.3A8 8 0 0 1 5.1 13zm6.9 6.9c-.9-1.2-1.8-3.6-1.9-6.9h3.8c-.1 3.3-1 5.7-1.9 6.9zm2.5-.6a15 15 0 0 0 1.4-6.3h3a8 8 0 0 1-4.4 6.3z"/></svg>
          www.maplegroveschools.com
        </li>
        <li class="contacts__item">
          <svg class="contacts__icon" viewBox="0 0 24 24" aria-hidden="true"><path d="M12 2a7 7 0 0 0-7 7c0 5.2 7 13 7 13s7-7.8 7-13a7 7 0 0 0-7-7zm0 9.5A2.5 2.5 0 1 1 12 6.5a2.5 2.5 0 0 1 0 5z"/></svg>
          48 Elm Avenue, Suite 3 Fairlen, MA 01699
        </li>
      </ul>
    </div>
  </section>
</body>
</html>
```